Maple Lantern Productions web site

I need to build a website for a new company I am launching next month. Maple Lantern Productions is a company based in New England that provides sound, lighting, and audio visual services to weddings, corporate, and any other cusomer base looking for quality service for a fair price. Looking for somebody to do a full site not just the image files. I am looking to keep the colors of my logo (orange and black) and possibly grey and white. I am looking to build my site very similar to brightvaleevents.example, which is owned by a friend of mine. I like how he has the big pictures that load in to the site and the basic menu items. I'll need a gallery of photos. The designs should communicate quality, value and trust.
My website address is maplelanternco.example.
Updates

Hi and thanks to everyone for posting such great ideas for our new design.I have some items that I'd like to ask you all to focus on in your revisions.I like how http://www.brightvaleevents.example/ website has five or six high res pictures that change in a slideshow format with a caption that loads in for each one for the different types of services. Try and capture pics like these and with teh same headings as he has. The basic menu designs have been interesting.I am more fond of the menus that are more white with some orange as I dont want it to be too dark. I'm curious to see how your galleries will work and if i'll be able to edit the pages myself? I have some more info on the company for you to fill in:website address is ciderhouseco.comemail: info@ciderhouseco.comaddress: Maple Lantern Productions57 Littlefield StreetAvon, MA 02417"New England's finest DJ's, lighting and sound, video and more. Creating memories one perfect event at a time."Put this under the loading pictures as a tagline.About Cider HouseCider House Productions is a collection of New England's finest talent, ready to make your next event the one you've dreamed of. We have the skills and expertise to deliver your vision of your perfect event. From elegant weddings to themed mitzvah's, corporate av, videography and detail lighting, we offer all of the elements to make your event a success. Added Wednesday, March 1, 2017

Designer's Please also make sure that your design flows well on any device it is being viewed on as well. Thanks. Added Wednesday, March 1, 2017

Project Deadline Extended Reason: Hello designerThank you all very much for your hard work on our project. Im sorry but i need to extend the date of my project. Our parent conpany Rook Nine Prodactions sponsors Bay Youth Assemblies and we are currently at their leadership conference on the Cape. I will be back in on Monday and with your help will get this finished by Thursday the 16th. Thanks Added Thursday, March 9, 2017

Project Deadline Extended Reason: One of the designers is not responding so I now have to make revisions with other designers. I hope to get this website done over the weekends so please get your revisions as soon as possible. Thank you. I am also upgrading the budget another $75 to hopefully get some more interest on my project. Added Wednesday, March 15, 2017

Target Market(s)

Wedding - Corporate -

Industry/Entity Type

It Company

Coding

Coded - Design and coding required

Number of Pages Required

5+ page

Font styles to use
Sans Serif

Requirements
Must have
• Photo Gallery - I want to be able to edit it myself
Nice to have
• I like the look of my friends website brightvaleevents.example

```html
<!DOCTYPE html>
<html lang="en">
<head>
<meta charset="utf-8">
<title>Maple Lantern Productions</title>
<link href="https://fonts.googleapis.com/css2?family=Roboto:wght@300;400;500;700&family=Montserrat:wght@500;600&display=swap" rel="stylesheet">
<style>
:root{
  --orange:#f2682a;
  --orange-soft:#f47a40;
  --ink:#222222;
  --text:#666666;
  --muted:#888888;
  --line:#e4e4e4;
  --pale:#f5f6f8;
  --footer:#f1f1f1;
  --bar:#2b2b2b;
  --white:#ffffff;
}
*{margin:0;padding:0;box-sizing:border-box}
html,body{width:1200px;height:3442px;overflow:hidden}
body{position:relative;background:var(--white);font-family:"Roboto",Arial,sans-serif;color:var(--text)}
.abs{position:absolute}
.btn{position:absolute;background:var(--orange);color:var(--white);font-size:13px;font-weight:500;text-transform:uppercase;display:flex;align-items:center;justify-content:center;border-radius:3px;letter-spacing:.2px}
.photo{position:absolute;border-radius:4px}

/* header */
.site-header{top:0;left:0;width:1200px;height:87px;background:var(--white);box-shadow:0 1px 4px rgba(0,0,0,.08);z-index:3}
.brand{left:87px;top:16px;display:flex;align-items:center;gap:10px}
.brand-mark{width:54px;height:54px;border-radius:50%;background:var(--orange)}
.brand-name{font-weight:700;font-size:17px;line-height:20px;color:var(--ink);letter-spacing:.5px;text-transform:uppercase}
.nav{top:0;left:505px;height:87px;display:flex;align-items:center;gap:0}
.nav a{font-size:12px;font-weight:500;color:var(--ink);text-decoration:none;text-transform:uppercase;margin-right:46px}
.nav a.active{color:var(--orange)}
.search{left:1067px;top:24px;width:44px;height:44px;border-radius:50%;background:var(--orange)}

/* hero */
.hero{top:87px;left:0;width:1200px;height:501px;background:linear-gradient(110deg,#e9ecef 0%,#dfe2e6 35%,#b9b2ad 60%,#3c3a3a 85%,#2a2a2a 100%)}
.hero-title{left:87px;top:243px;font-size:60px;font-weight:300;color:var(--orange);letter-spacing:.5px}
.hero-text{left:87px;top:318px;width:420px;font-size:12px;line-height:22px;color:var(--white)}
.arrow{top:308px;width:52px;height:52px;border-radius:50%;border:2px solid var(--white)}

/* headings */
.sec-title{position:absolute;left:0;width:1200px;text-align:center;font-size:25px;font-weight:300;color:var(--ink);text-transform:uppercase;letter-spacing:.5px}
.sec-title span{color:var(--orange)}
.sec-sub{position:absolute;left:0;width:1200px;text-align:center;font-size:12px;color:var(--text)}
.para{position:absolute;font-size:12px;line-height:26px;color:var(--text)}

/* services */
.services{top:863px;left:0;width:1200px;height:1441px;background:var(--pale)}
.svc-title{position:absolute;font-family:"Montserrat",Arial,sans-serif;font-size:17px;font-weight:600;color:var(--ink);text-transform:uppercase}
.svc-rule{position:absolute;width:60px;height:2px;background:var(--orange)}
.divider{position:absolute;left:103px;width:994px;height:1px;background:var(--line)}

/* about */
.about{top:2304px;left:0;width:1200px;height:276px;background:linear-gradient(90deg,#f06a2c,#f47b3e 50%,#f06a2c)}
.about .sec-title{color:var(--white)}
.btn-ghost{position:absolute;border:1px solid var(--white);color:var(--white);font-size:12px;text-transform:uppercase;display:flex;align-items:center;justify-content:center}

/* footer */
.footer{top:3094px;left:0;width:1200px;height:280px;background:var(--footer)}
.foot-head{position:absolute;font-family:"Montserrat",Arial,sans-serif;font-size:15px;font-weight:600;color:var(--ink);text-transform:uppercase;letter-spacing:.5px}
.foot-line{position:absolute;font-size:12px;color:var(--ink);display:flex;align-items:center;gap:12px}
.foot-line svg{flex:none}
.email{position:absolute;left:650px;top:3324px;width:213px;height:34px;background:var(--white);border:1px solid #dcdcdc;font-size:12px;color:var(--muted);padding-left:10px;display:flex;align-items:center}
.social{position:absolute;top:3356px;width:36px;height:36px;border-radius:50%;border:1px solid #b8b8b8}
.copyright{top:3374px;left:0;width:1200px;height:68px;background:var(--bar);color:#d8d8d8;font-size:12px;display:flex;align-items:center;justify-content:center}
</style>
</head>
<body>

<header class="abs site-header">
  <div class="abs brand">
    <div class="brand-mark"></div>
    <div class="brand-name">Maple Lantern<br>Productions</div>
  </div>
  <nav class="abs nav">
    <a class="active">Home</a><a>About Us</a><a>Services</a><a>Events</a><a>Gallery</a><a>Contact Us</a>
  </nav>
  <div class="abs search">
    <svg width="44" height="44" viewBox="0 0 44 44"><circle cx="20" cy="20" r="5" fill="none" stroke="#fff" stroke-width="2"/><line x1="24" y1="24" x2="28" y2="28" stroke="#fff" stroke-width="2.4" stroke-linecap="round"/></svg>
  </div>
</header>

<section class="abs hero" role="img" aria-label="Bride and groom seen from above holding a bouquet of pink roses"></section>
<h1 class="abs hero-title">MAPLE LANTERN</h1>
<p class="abs hero-text">Sed ut perspiciatis unde omnis iste natus error sit voluptatem accusantium doloremque laudantium, totam rem. quae ab illo inventore veritatis et quasi architecto beatae vitae dicta sunt explicabo.</p>
<div class="btn" style="left:87px;top:415px;width:136px;height:36px">Read More</div>
<div class="abs arrow" style="left:24px"><svg width="48" height="48" viewBox="0 0 48 48"><polyline points="27,16 19,24 27,32" fill="none" stroke="#fff" stroke-width="2.4"/></svg></div>
<div class="abs arrow" style="left:1122px"><svg width="48" height="48" viewBox="0 0 48 48"><polyline points="21,16 29,24 21,32" fill="none" stroke="#fff" stroke-width="2.4"/></svg></div>

<!-- welcome -->
<h2 class="sec-title" style="top:630px">Welcome to <span>Maple Lantern Productions</span></h2>
<p class="para" style="left:260px;top:676px;width:680px;text-align:center">Sed ut perspiciatis unde omnis iste natus error sit voluptatem accusantium doloremque laudantium, totam rem aperiam, eaque ipsa quae ab illo inventore veritatis et quasi architecto beatae vitae dicta sunt explicabo. Nemo enim ipsam aut consequuntur magni dolores eos qui ratione voluptatem sequi nesciunt</p>
<div class="btn" style="left:519px;top:773px;width:162px;height:44px">Read More Info</div>

<!-- services -->
<section class="abs services"></section>
<h2 class="sec-title" style="top:890px">Our <span>Services</span></h2>
<p class="sec-sub" style="top:933px">Sed ut perspiciatis unde omnis iste natus error sit voluptatem accusantium doloremque laudantium.</p>

<div class="photo" style="left:103px;top:996px;width:418px;height:255px;background:linear-gradient(180deg,#4a3a28,#8a6a3e 40%,#2a2622 70%,#151515)" role="img" aria-label="Sound mixing desk in front of a stage"></div>
<h3 class="svc-title" style="left:583px;top:1005px">Sound Services</h3>
<div class="svc-rule" style="left:583px;top:1039px"></div>
<p class="para" style="left:585px;top:1062px;width:510px">Sed ut perspiciatis unde omnis iste natus error sit voluptatem accusantium doloremque laudantium, totam rem aperiam, eaque ipsa quae ab illo inventore veritatis et quasi architecto beatae vitae dicta sunt explicabo. Nemo enim ipsam voluptatem quia voluptas sit aspernatur la consequuntur magni dolores eos qui ratione voluptatem sequi nesciunt.</p>
<div class="btn" style="left:585px;top:1187px;width:133px;height:45px">Read More Info</div>

<div class="divider" style="top:1292px"></div>

<h3 class="svc-title" style="left:103px;top:1341px">Lighting Services</h3>
<div class="svc-rule" style="left:103px;top:1375px"></div>
<p class="para" style="left:105px;top:1396px;width:510px">Sed ut perspiciatis unde omnis iste natus error sit voluptatem accusantium doloremque laudantium, totam rem aperiam, eaque ipsa quae ab illo inventore veritatis et quasi architecto beatae vitae dicta sunt explicabo. Nemo enim ipsam voluptatem quia voluptas sit aspernatur la consequuntur magni dolores eos qui ratione voluptatem sequi nesciunt.</p>
<div class="btn" style="left:105px;top:1520px;width:133px;height:45px">Read More Info</div>
<div class="photo" style="left:679px;top:1331px;width:418px;height:255px;background:linear-gradient(180deg,#b89ee0,#8a5fd0 45%,#6a3cb6 75%,#d9cdf0)" role="img" aria-label="Banquet hall lit in purple with draped ceiling"></div>

<div class="divider" style="top:1627px"></div>

<div class="photo" style="left:103px;top:1666px;width:418px;height:255px;background:linear-gradient(160deg,#2a4a6a,#4d7fa8 40%,#1e1e24 70%,#0e0e12)" role="img" aria-label="DJ controller and laptop lit in blue"></div>
<h3 class="svc-title" style="left:583px;top:1675px">Audio Services</h3>
<div class="svc-rule" style="left:583px;top:1709px"></div>
<p class="para" style="left:585px;top:1732px;width:510px">Sed ut perspiciatis unde omnis iste natus error sit voluptatem accusantium doloremque laudantium, totam rem aperiam, eaque ipsa quae ab illo inventore veritatis et quasi architecto beatae vitae dicta sunt explicabo. Nemo enim ipsam voluptatem quia voluptas sit aspernatur la consequuntur magni dolores eos qui ratione voluptatem sequi nesciunt.</p>
<div class="btn" style="left:585px;top:1857px;width:133px;height:45px">Read More Info</div>

<div class="divider" style="top:1962px"></div>

<h3 class="svc-title" style="left:103px;top:2011px">Visual Services</h3>
<div class="svc-rule" style="left:103px;top:2045px"></div>
<p class="para" style="left:105px;top:2066px;width:510px">Sed ut perspiciatis unde omnis iste natus error sit voluptatem accusantium doloremque laudantium, totam rem aperiam, eaque ipsa quae ab illo inventore veritatis et quasi architecto beatae vitae dicta sunt explicabo. Nemo enim ipsam voluptatem quia voluptas sit aspernatur la consequuntur magni dolores eos qui ratione voluptatem sequi nesciunt.</p>
<div class="btn" style="left:105px;top:2190px;width:133px;height:45px">Read More Info</div>
<div class="photo" style="left:679px;top:2001px;width:418px;height:255px;background:linear-gradient(135deg,#9a9a9e,#5a5458 40%,#c9c3be 70%,#3a3638)" role="img" aria-label="Collage of wedding portrait photographs"></div>

<!-- about -->
<section class="abs about" role="img" aria-label="Orange tinted reception hall background"></section>
<h2 class="sec-title" style="top:2343px;color:var(--white)">About Us</h2>
<p class="para" style="left:230px;top:2388px;width:740px;text-align:center;color:var(--white)">Sed ut perspiciatis unde omnis iste natus error sit voluptatem accusantium doloremque laudantium, totam rem aperiam, eaque ipsa quae ab illo inventore veritatis et quasi architecto beatae vitae dicta sunt explicabo. Nemo enim ipsam voluptatem quia voluptas sit sed quia consequuntur magni dolores eos qui ratione voluptatem sequi nesciunt.</p>
<div class="btn-ghost" style="left:487px;top:2490px;width:227px;height:44px">Click Here For More Info</div>

<!-- gallery -->
<h2 class="sec-title" style="top:2618px">Photo <span>Gallery</span></h2>
<p class="sec-sub" style="top:2661px">Sed ut perspiciatis unde omnis iste natus error sit voluptatem accusantium doloremque laudantium.</p>
<div class="abs" style="left:87px;top:2701px;width:505px;height:165px;background:linear-gradient(90deg,#1a1c2c,#3a3f6a 30%,#14141c 60%,#4a4c6e)" role="img" aria-label="Couple dancing under sparkler fountains"></div>
<div class="abs" style="left:604px;top:2701px;width:250px;height:342px;background:linear-gradient(180deg,#1c2414,#5a6a2a 40%,#c9b060 65%,#3a3424)" role="img" aria-label="Garden walkway under an arch of string lights"></div>
<div class="abs" style="left:865px;top:2701px;width:248px;height:165px;background:linear-gradient(180deg,#3a2c1c,#b8946a 50%,#e6e0d6)" role="img" aria-label="Reception tables under warm hanging lights"></div>
<div class="abs" style="left:87px;top:2876px;width:248px;height:167px;background:linear-gradient(180deg,#5a4020,#8a6a40 45%,#1c1a18)" role="img" aria-label="Stage and sound desk at an event"></div>
<div class="abs" style="left:347px;top:2876px;width:245px;height:167px;background:linear-gradient(135deg,#2a2a2a,#6a5a48 50%,#1a1a1a)" role="img" aria-label="Musician playing acoustic guitar"></div>
<div class="abs" style="left:865px;top:2876px;width:248px;height:167px;background:linear-gradient(135deg,#1a1a1a,#a88a40 50%,#e8e4dc)" role="img" aria-label="Saxophone player in a suit"></div>

<!-- footer -->
<footer class="abs footer"></footer>
<div class="abs" style="left:180px;top:3133px;width:100px;height:100px;border-radius:50%;background:var(--orange)"></div>
<div class="abs" style="left:90px;top:3246px;width:280px;text-align:center;font-weight:700;font-size:27px;line-height:30px;color:var(--ink);text-transform:uppercase">Maple Lantern<br>Productions</div>

<h4 class="foot-head" style="left:406px;top:3144px">Contact Us</h4>
<div class="foot-line" style="left:406px;top:3190px"><svg width="14" height="14" viewBox="0 0 14 14"><path d="M3 1l3 3-2 2c1 2 2 3 4 4l2-2 3 3-2 2C6 13 1 8 1 3z" fill="#555"/></svg>(000)-121-1231 (Phone)</div>
<div class="foot-line" style="left:406px;top:3219px"><svg width="14" height="14" viewBox="0 0 14 14"><rect x="2" y="4" width="10" height="8" fill="#555"/><rect x="4" y="1" width="6" height="3" fill="#555"/></svg>(000)-121-1231 (Fax)</div>
<div class="foot-line" style="left:406px;top:3248px"><svg width="14" height="14" viewBox="0 0 14 14"><rect x="1" y="3" width="12" height="8" fill="none" stroke="#555" stroke-width="1.4"/><polyline points="1,3 7,8 13,3" fill="none" stroke="#555" stroke-width="1.4"/></svg><span style="text-decoration:underline">info@maplelanternco.example</span></div>
<div class="foot-line" style="left:406px;top:3277px;align-items:flex-start"><svg width="14" height="14" viewBox="0 0 14 14"><path d="M7 1a4 4 0 0 1 4 4c0 3-4 8-4 8S3 8 3 5a4 4 0 0 1 4-4z" fill="#555"/></svg><span style="line-height:15px">#24 Lorem Ipsum Dummy<br>Lorem Ipsum</span></div>

<h4 class="foot-head" style="left:650px;top:3144px">Newsletter</h4>
<p class="abs" style="left:650px;top:3182px;width:220px;font-size:12px;line-height:20px;color:var(--ink)">Register Your email address to get information about us</p>
<div class="email">Email Address</div>
<div class="btn" style="left:650px;top:3286px;width:82px;height:26px;font-size:11px;border-radius:2px">Subscribe</div>

<h4 class="foot-head" style="left:907px;top:3144px">Follow Us</h4>
<p class="abs" style="left:907px;top:3184px;width:200px;font-size:11px;line-height:18px;color:var(--ink)">Lorem ipsum dolor sit amet, conse ctetur adipiscing elit. Nulla in purus nibh. Donec ornare</p>
<div class="social" style="left:907px;top:3259px"></div>
<div class="social" style="left:949px;top:3259px"></div>
<div class="social" style="left:991px;top:3259px"></div>
<div class="social" style="left:1033px;top:3259px"></div>
<div class="social" style="left:1075px;top:3259px"></div>

<div class="abs copyright">© Copyright 2017 Maple Lantern co. All Rights Reserved</div>

</body>
</html>
```